Will you marry me post card

I am just looking for a postcard to send my partner that will ask him to marry me.
I plan on creating about 200 of them and mailing them all at once so that he gets them all on the same day.
They should all be similar or could have a few different options.
I would like it simple, elegant, clean and crisp. No images, just text or icons

My only requirement is the text, "will you marry me?" in all lowercase -- any fonts, can be big, small, varying sizes, repeated, whole card, tiny space, don't care...just amazing design. BUT SIMPLE!

```html
<!DOCTYPE html>
<html lang="en">
<head>
<meta charset="utf-8">
<title>will you marry me? — postcard</title>
<link rel="stylesheet" href="https://fonts.googleapis.com/css2?family=Raleway:wght@200&display=swap">
<style>
  :root {
    --backdrop: #efeae4;
    --peach-light: #fff3e3;
    --peach: #fde6c6;
    --peach-edge: #f6cf9e;
    --cocoa: #6b3a2f;
    --cocoa-light: #86504a;
    --ink: #5a2e24;
  }
  * { margin: 0; padding: 0; box-sizing: border-box; }
  html, body {
    width: 1200px;
    height: 548px;
    overflow: hidden;
    background: var(--backdrop);
  }
  .postcard {
    position: absolute;
    left: 75px;
    top: 72px;
    width: 1050px;
    height: 403px;
    display: flex;
  }
  .postcard__front {
    position: relative;
    width: 525px;
    height: 100%;
    background: radial-gradient(ellipse at 52% 45%, var(--peach-light) 0%, var(--peach) 60%, var(--peach-edge) 100%);
    overflow: hidden;
  }
  .front__ornament {
    position: absolute;
    left: 40px;
    top: 30px;
    width: 460px;
    height: 340px;
    border-radius: 50%;
    background: radial-gradient(ellipse at center, rgba(255,255,255,0.45) 0%, rgba(255,255,255,0.15) 55%, rgba(255,255,255,0) 75%);
  }
  .proposal {
    position: absolute;
    left: 180px;
    top: 90px;
    font-family: "Raleway", sans-serif;
    font-weight: 200;
    font-size: 72px;
    line-height: 52px;
    letter-spacing: -2.5px;
    color: var(--ink);
  }
  .proposal__line { display: block; white-space: nowrap; }
  .proposal__line--will { margin-left: 18px; }
  .proposal__line--you { margin-left: 0; }
  .proposal__line--marry { margin-left: 12px; }
  .proposal__line--me { margin-left: 6px; }
  .postcard__back {
    width: 525px;
    height: 100%;
    background: linear-gradient(135deg, var(--cocoa-light) 0%, var(--cocoa) 50%, var(--cocoa-light) 100%);
  }
</style>
</head>
<body>
  <main class="postcard">
    <section class="postcard__front">
      <div class="front__ornament" role="img" aria-label="Faint white lace flourish ornament behind the text"></div>
      <h1 class="proposal">
        <span class="proposal__line proposal__line--will">will</span>
        <span class="proposal__line proposal__line--you">you</span>
        <span class="proposal__line proposal__line--marry">marry</span>
        <span class="proposal__line proposal__line--me">me?</span>
      </h1>
    </section>
    <section class="postcard__back" role="img" aria-label="Tone-on-tone brown swirling flourish pattern"></section>
  </main>
</body>
</html>
```